Harborline Auto LLC

Car Dealer Customer Service
Address: 2874 Cresthaven Road, Shelbyville, TN 37162
web: www.harborlineautoxq.net
email: harborlineautoxq@mailnest.example
Phone: (931) 555-0148
Phone: (629) 555-0173

```html
<!DOCTYPE html>
<html lang="en">
<head>
<meta charset="utf-8">
<title>Harborline Auto – Business Card</title>
<link rel="stylesheet" href="https://fonts.googleapis.com/css2?family=Krona+One&family=Arimo:wght@400;700&display=swap">
<style>
  :root {
    --stage: #1f1f1f;
    --brand-blue: #1e78aa;
    --brand-blue-light: #2a8fc7;
    --brand-yellow: #e9b347;
    --paper: #ffffff;
    --ink: #1a1a1a;
    --rule: #c9c9c9;
  }
  * { box-sizing: border-box; margin: 0; padding: 0; }
  html, body { width: 1200px; height: 1015px; overflow: hidden; }
  body {
    background: radial-gradient(ellipse at 50% 40%, #333 0%, var(--stage) 70%);
    font-family: "Arimo", Arial, sans-serif;
    position: relative;
  }
  .card {
    position: absolute;
    left: 250px;
    width: 700px;
    height: 400px;
    overflow: hidden;
    box-shadow: 0 14px 30px rgba(0,0,0,.55);
  }
  /* Front */
  .card--front { top: 70px; background: var(--brand-blue); }
  .front__mark {
    position: absolute; left: 50%; top: 58px;
    width: 110px; height: 110px; margin-left: -55px;
    border-radius: 50%; background: var(--paper);
  }
  .front__name {
    position: absolute; left: 0; right: 0; top: 192px;
    text-align: center; color: var(--paper);
    font-family: "Krona One", sans-serif; font-size: 34px; letter-spacing: 1px;
  }
  .front__band {
    position: absolute; left: 0; right: 0; top: 268px; height: 52px;
    background: var(--brand-yellow);
    display: flex; align-items: center; justify-content: center;
    color: var(--paper);
    font-family: "Krona One", sans-serif; font-size: 17px; letter-spacing: 4px;
  }
  /* Back */
  .card--back { top: 530px; background: var(--paper); }
  .back__brand {
    position: absolute; left: 30px; top: 110px; width: 330px;
    display: flex; flex-direction: column; align-items: center;
  }
  .back__mark { width: 86px; height: 86px; border-radius: 50%; background: var(--brand-blue-light); }
  .back__name {
    margin-top: 22px; color: var(--brand-blue);
    font-family: "Krona One", sans-serif; font-size: 19px; white-space: nowrap;
  }
  .back__divider {
    position: absolute; left: 378px; top: 70px; width: 1px; height: 220px;
    background: var(--rule);
  }
  .contact { position: absolute; left: 402px; top: 66px; color: var(--ink); }
  .contact__name {
    font-family: "Krona One", sans-serif; font-size: 16px; color: var(--brand-blue);
  }
  .contact__title { font-size: 14px; color: var(--brand-yellow); margin-top: 2px; }
  .contact__address { font-size: 14px; line-height: 1.3; margin-top: 14px; }
  .contact__list { list-style: none; margin-top: 16px; font-size: 14px; line-height: 1.55; }
  .contact__list li { display: flex; align-items: center; gap: 7px; }
  .contact__list svg { width: 13px; height: 13px; flex: none; }
  .back__stripe {
    position: absolute; left: 0; right: 0; bottom: 0; height: 18px;
    background: var(--brand-yellow);
  }
  .back__web-tab {
    position: absolute; right: 0; bottom: 0; width: 300px; height: 50px;
    background: linear-gradient(90deg, var(--brand-blue), var(--brand-blue-light));
    border-left: 6px solid var(--paper);
    display: flex; align-items: center; justify-content: center;
    color: var(--paper); font-size: 15px;
  }
</style>
</head>
<body>
  <section class="card card--front" aria-label="Business card front">
    <div class="front__mark"></div>
    <div class="front__name">HARBORLINE AUTO</div>
    <div class="front__band">CAR DEALER CUSTOMER SERVICE</div>
  </section>

  <section class="card card--back" aria-label="Business card back">
    <div class="back__brand">
      <div class="back__mark"></div>
      <div class="back__name">HARBORLINE AUTO</div>
    </div>
    <div class="back__divider"></div>
    <div class="contact">
      <div class="contact__name">MARCUS DELANEY</div>
      <div class="contact__title">Managing Director</div>
      <p class="contact__address">2874 Cresthaven Road<br>Shelbyville, TN 37162</p>
      <ul class="contact__list">
        <li><svg viewBox="0 0 24 24" fill="var(--brand-blue-light)"><path d="M6.6 10.8a15 15 0 0 0 6.6 6.6l2.2-2.2a1 1 0 0 1 1-.25 11.4 11.4 0 0 0 3.6.57 1 1 0 0 1 1 1V20a1 1 0 0 1-1 1A17 17 0 0 1 3 4a1 1 0 0 1 1-1h3.5a1 1 0 0 1 1 1c0 1.25.2 2.45.57 3.57a1 1 0 0 1-.25 1z"/></svg>(931) 555-0148</li>
        <li><svg viewBox="0 0 24 24" fill="var(--brand-blue-light)"><path d="M6.6 10.8a15 15 0 0 0 6.6 6.6l2.2-2.2a1 1 0 0 1 1-.25 11.4 11.4 0 0 0 3.6.57 1 1 0 0 1 1 1V20a1 1 0 0 1-1 1A17 17 0 0 1 3 4a1 1 0 0 1 1-1h3.5a1 1 0 0 1 1 1c0 1.25.2 2.45.57 3.57a1 1 0 0 1-.25 1z"/></svg>(629) 555-0173</li>
        <li><svg viewBox="0 0 24 24" fill="var(--brand-blue-light)"><path d="M2 5h20v14H2z M2 5l10 8 10-8" stroke="#fff" stroke-width="1.5"/></svg>harborlineautoxq@mailnest.example</li>
      </ul>
    </div>
    <div class="back__stripe"></div>
    <div class="back__web-tab">www.harborlineautoxq.net</div>
  </section>
</body>
</html>
```